red maple heating & air company flyer for listbazaar ad

size should be 1200x900
this is an ac company, we have a logo but not necessary to use
we offer free estimates, we are open 24/7, fast and affordable
service, licensed and insured
we sell all brands and service all
we offer services for refrigeration residential and commercial
I will post a few of my ads I made but need a pros idea

Red Maple Heating & Air Company
407-318-5274
redmapleair@quorvanmail.com
redmapleair247.com
license # must be on flyer state law it is CAC2739561
if you use the logo please remove the building

Target Market(s)

any one who needs has an ac in home

Industry/Entity Type

Hvac

Requirements
Must have
• contact info must be big

```html
<!DOCTYPE html>
<html lang="en">
<head>
<meta charset="utf-8">
<title>Red Maple Heating &amp; Air Company</title>
<link href="https://fonts.googleapis.com/css2?family=Arimo:ital,wght@0,400;0,700;1,700&display=swap" rel="stylesheet">
<style>
  :root {
    --lavender-light: #eceaff;
    --lavender: #a9a8f5;
    --violet: #5d5ef0;
    --sky-top: #7aa6f7;
    --sky-mid: #5f8ef0;
    --sky-low: #c9d6f7;
    --night: #070b30;
    --navy: #141a8c;
    --ink: #0d1b3d;
    --heading: #143563;
    --red: #d8141c;
    --white: #ffffff;
    --brand-grey: #c9d3ea;
    --curve-edge: #eef1ff;
  }
  * { margin: 0; padding: 0; box-sizing: border-box; }
  html, body { width: 1200px; height: 900px; overflow: hidden; background: #fff; }
  .flyer {
    position: relative; width: 1200px; height: 900px; overflow: hidden;
    font-family: "Arimo", Arial, sans-serif;
    background: linear-gradient(155deg, var(--lavender-light) 0%, var(--lavender) 45%, var(--violet) 100%);
  }
  .flyer > * { z-index: 2; }
  .flyer > svg.backdrop { position: absolute; inset: 0; z-index: 0; }
  .license {
    position: absolute; top: 9px; right: 12px;
    color: var(--white); font-weight: 700; font-size: 13px; letter-spacing: .3px;
  }
  .company-name {
    position: absolute; left: 100px; top: 118px; width: 400px;
    display: flex; align-items: center; gap: 16px;
    color: var(--red); font-weight: 700; font-size: 44px; line-height: 1.05;
  }
  .company-name .mark {
    flex: none; width: 34px; height: 34px; border-radius: 50%; background: var(--red);
  }
  .sectors {
    position: absolute; left: 748px; top: 76px;
    color: var(--heading); font-weight: 700; font-size: 38px; line-height: 66px; letter-spacing: 1.5px;
  }
  .brands {
    position: absolute; left: 600px; top: 262px; width: 600px; height: 150px; color: var(--white);
  }
  .brands h2 { font-weight: 400; font-size: 26px; letter-spacing: -.3px; margin-top: 16px; }
  .brands ul {
    list-style: none; display: flex; align-items: center;
    column-gap: 10px; margin-top: 16px; font-size: 14px; font-weight: 700;
    color: var(--brand-grey);
  }
  .brands ul + ul { margin-top: 18px; }
  .brands li { display: flex; align-items: center; gap: 10px; }
  .brands li + li::before { content: "•"; color: var(--white); font-size: 10px; }
  .brands .plain-badge { width: 16px; height: 16px; background: var(--brand-grey); display: inline-block; }
  .estimates {
    position: absolute; left: 0; top: 416px; width: 598px; height: 84px; background: var(--night);
    color: var(--white); font-weight: 700; font-size: 46px; line-height: 84px; padding-left: 92px;
  }
  .phone {
    position: absolute; left: 32px; top: 514px;
    color: var(--navy); font-weight: 700; font-size: 84px; letter-spacing: 1.5px;
  }
  .service { position: absolute; left: 36px; top: 690px; font-style: italic; font-weight: 700; }
  .service .hours { color: var(--red); font-size: 46px; line-height: 48px; }
  .service .promise { color: var(--ink); font-size: 44px; line-height: 52px; letter-spacing: 1.5px; }
  .credentials {
    position: absolute; left: 660px; top: 476px;
    color: var(--navy); font-style: italic; font-weight: 700; font-size: 31px; letter-spacing: .5px;
  }
  .equipment-photo {
    position: absolute; left: 770px; top: 540px; width: 430px; height: 360px; z-index: 1;
    background: linear-gradient(160deg, #d8dee8 0%, #9aa3b0 55%, #6d7482 100%);
    border-radius: 40px 0 0 0;
  }
  .contact {
    position: absolute; left: 32px; top: 846px;
    color: var(--white); font-weight: 700; font-size: 25px; display: flex; gap: 14px; align-items: center;
  }
  .contact .dot { width: 8px; height: 8px; border-radius: 50%; background: var(--white); }
</style>
</head>
<body>
<main class="flyer">
  <svg class="backdrop" width="1200" height="900" viewBox="0 0 1200 900" aria-hidden="true">
    <defs>
      <linearGradient id="skyPanel" x1="0" y1="0" x2="0" y2="1">
        <stop offset="0" stop-color="#7aa6f7"/>
        <stop offset=".3" stop-color="#5f8ef0"/>
        <stop offset=".5" stop-color="#c9d6f7"/>
        <stop offset="1" stop-color="#a8baf2"/>
      </linearGradient>
    </defs>
    <path d="M700 0 C620 150 560 380 640 560 C690 660 760 720 860 780 L1200 900 L1200 0 Z"
          fill="url(#skyPanel)" stroke="#eef1ff" stroke-width="10"/>
    <rect x="592" y="258" width="608" height="157" fill="#070b30"/>
  </svg>

  <p class="license">LICENSE: CAC2739561</p>

  <h1 class="company-name"><span class="mark"></span>Red Maple Heating &amp; Air Company</h1>

  <p class="sectors">Residential and<br>Commercial</p>

  <section class="brands">
    <h2>We repair and service these brands + more,</h2>
    <ul>
      <li>TRAVALE</li><li>Corriton</li><li>Brynell</li><li>Amoria</li><li>LENHART</li><li>Reemac</li><li>RUDELL</li>
    </ul>
    <ul>
      <li>YORVANE</li><li>TEMPORA</li><li><span class="plain-badge"></span></li><li>Amerent Std</li><li>Goodvale</li><li>Colbrook</li><li>DUVERNE</li>
    </ul>
  </section>

  <p class="estimates">FREE ESTIMATES</p>
  <p class="phone">407-318-5274</p>

  <div class="service">
    <p class="hours">24/7</p>
    <p class="promise">FAST &amp; AFFORDABLE SERVICE</p>
  </div>

  <p class="credentials">Licensed &amp; Insured</p>

  <div class="equipment-photo" role="img" aria-label="Technician in overalls standing beside solar panels, an outdoor AC condenser, a mini-split unit and a furnace"></div>

  <p class="contact"><span>www.redmapleair247.com</span><span class="dot"></span><span>redmapleair@quorvanmail.com</span></p>
</main>
</body>
</html>
```